Business Card for Brenwickpartners

Need to design a business card with attached logo

Target Market(s)

I'm a financial/Investment adviser so card must be professional

Industry/Entity Type

Business

Font styles to use
Serif
Sans Serif

Requirements
Must have
• Would like in include the GOLD version of my logo if possible

Tobin Brenwick
President

Address is
4127 Verlane Blvd
San Ramon, Ca. 94583

Phone
510-555-0147
Fax
925-555-0183

Email
tobin@brenwickpartners.example

I also need the following tag line at the bottom of card:

Investment Advisor Representative of and Securities offered
through Halvern Capital Brokerage, LLC Member QUDEX, TRAB
and Registered Investment Advisor.

Nice to have
• Split color in order to incorporate GOLD LOGO
Should not have

```html
<!DOCTYPE html>
<html lang="en">
<head>
<meta charset="utf-8">
<title>Brenwick Partners – Business Card</title>
<link rel="stylesheet" href="https://fonts.googleapis.com/css2?family=Tinos:ital,wght@0,400;1,400;1,700&family=Open+Sans:wght@300;400&display=swap">
<style>
  :root {
    --backdrop-light: #f4f4f4;
    --backdrop-dark: #c9c9c9;
    --card: #4b4b4d;
    --card-deep: #444446;
    --card-back: #555557;
    --gold-light: #e9d79a;
    --gold: #c9a75a;
    --gold-deep: #8f7136;
    --ink-light: #f2f2f2;
    --ink-muted: #b9b9b9;
    --rule: rgba(201, 167, 90, 0.55);
    --rule-soft: rgba(255, 255, 255, 0.18);
  }
  * { box-sizing: border-box; margin: 0; padding: 0; }
  html, body { width: 1200px; height: 787px; overflow: hidden; }
  body {
    background: radial-gradient(ellipse at 50% 40%, var(--backdrop-light) 0%, var(--backdrop-dark) 100%);
    position: relative;
    font-family: "Tinos", "Times New Roman", serif;
  }
  .card-set {
    position: absolute; left: 20px; top: 233px;
    display: flex; gap: 40px;
  }
  .business-card {
    position: relative;
    width: 560px; height: 320px;
    box-shadow: 0 8px 22px rgba(0,0,0,0.28);
    overflow: hidden;
  }
  .card-front { background: linear-gradient(180deg, var(--card) 0%, var(--card-deep) 100%); }
  .card-back {
    background: var(--card-back);
    display: flex; flex-direction: column; align-items: center; justify-content: center; gap: 16px;
  }
  .gold-band {
    position: absolute; left: 0; top: 0; width: 100%; height: 13px;
    background: linear-gradient(90deg, var(--gold-deep), var(--gold-light) 35%, var(--gold) 60%, var(--gold-light) 85%, var(--gold-deep));
  }
  .brand {
    position: absolute; left: 30px; top: 34px; width: 180px;
    display: flex; flex-direction: column; align-items: center; gap: 9px;
  }
  .brand-dot, .back-dot {
    border-radius: 50%;
    background: linear-gradient(135deg, var(--gold-light), var(--gold) 50%, var(--gold-deep));
  }
  .brand-dot { width: 42px; height: 42px; }
  .brand-name { font-size: 15px; letter-spacing: 0.6px; color: var(--gold); white-space: nowrap; }
  .back-dot { width: 110px; height: 110px; }
  .back-name { font-size: 22px; letter-spacing: 1px; color: var(--gold); }
  .holder { position: absolute; right: 40px; top: 58px; }
  .holder-name { font-size: 24px; color: var(--ink-light); line-height: 1; }
  .holder-title {
    font-family: "Open Sans", Arial, sans-serif; font-weight: 300;
    font-size: 12px; color: var(--ink-muted); text-align: right; margin-top: 1px;
  }
  .header-rule {
    position: absolute; left: 0; top: 126px; width: 100%; height: 2px;
    background: linear-gradient(90deg, transparent, var(--gold) 8%, var(--gold-light) 50%, var(--gold) 92%, transparent);
  }
  .address { position: absolute; right: 26px; top: 213px; font-size: 12.5px; color: var(--gold); }
  .rule { position: absolute; left: 20px; right: 12px; height: 1px; background: var(--rule); }
  .rule.upper { top: 230px; }
  .rule.lower { top: 274px; background: var(--rule-soft); }
  .disclosure {
    position: absolute; left: 16px; top: 233px; width: 246px;
    font-style: italic; font-weight: 700; font-size: 8.6px; line-height: 1.2; color: var(--ink-light);
    text-align: center;
  }
  .contact {
    position: absolute; left: 300px; top: 233px;
    font-size: 12px; color: var(--ink-light); line-height: 1.5;
  }
  .contact-line { display: flex; align-items: center; gap: 4px; }
  .contact-line svg { width: 11px; height: 11px; fill: var(--ink-light); flex: none; }
  .contact-line .gap { width: 6px; }
</style>
</head>
<body>
  <div class="card-set">
    <main class="business-card card-front">
      <div class="gold-band"></div>

      <div class="brand">
        <span class="brand-dot"></span>
        <span class="brand-name">BRENWICK PARTNERS</span>
      </div>

      <div class="holder">
        <p class="holder-name">Tobin Brenwick</p>
        <p class="holder-title">President</p>
      </div>

      <div class="header-rule"></div>

      <p class="address">4127 Verlane Blvd, San Ramon, Ca. 94583</p>
      <div class="rule upper"></div>

      <p class="disclosure">Investment Advisor Representative of and Securities offered through Halvern Capital Brokerage, LLC Member QUDEX, TRAB and Registered Investment Advisor.</p>

      <div class="contact">
        <p class="contact-line">
          <svg viewBox="0 0 24 24" aria-label="Phone"><path d="M6.6 10.8a15 15 0 0 0 6.6 6.6l2.2-2.2c.3-.3.7-.4 1-.2 1.1.4 2.3.6 3.6.6.6 0 1 .4 1 1V20c0 .6-.4 1-1 1A17 17 0 0 1 3 4c0-.6.4-1 1-1h3.5c.6 0 1 .4 1 1 0 1.3.2 2.5.6 3.6.1.3 0 .7-.2 1z"/></svg>
          <span>510-555-0147</span>
          <span class="gap"></span>
          <svg viewBox="0 0 24 24" aria-label="Fax"><path d="M7 3h8l3 3v4H7zM4 10h16a2 2 0 0 1 2 2v6h-4v3H6v-3H2v-6a2 2 0 0 1 2-2zm4 6v3h8v-3z"/></svg>
          <span>925-555-0183</span>
        </p>
        <p class="contact-line">
          <svg viewBox="0 0 24 24" aria-label="Email"><path d="M2 5h20v14H2zm2 2v.5l8 5 8-5V7zm0 2.8V17h16V9.8l-8 5z"/></svg>
          <span>tobin@brenwickpartners.example</span>
        </p>
      </div>
      <div class="rule lower"></div>
    </main>

    <section class="business-card card-back">
      <span class="back-dot"></span>
      <span class="back-name">BRENWICK PARTNERS</span>
    </section>
  </div>
</body>
</html>
```